Refresh Velquor Web Presence - www.velquor-sample.com

Velquor (www.velquor-sample.com)web site needs a makeover. It needs to be more modern, less cluttered, more corporate, prestigious, user friendly, impressive, up to date. We want a modern corporate image that encourages our business users to trust us and buy our products and services. They need to understand that they are dealing with a highly reputable, long established company, but one that is up to date and forward thinking.
1. Clean uncluttered design.
2. Domain Registration box and Countries (price) box to be collapsible and expandable.
3. All links on page need to be conserved for SEO but hidden from view.
4. Logo and general colour scheme need to be retained.
5. Phone number to be prominently displayed at top of page.
6. No calls to action (CTA) below the fold.
7. Sites we like: www.brinzal-sample.com, www.tundexa-sample.com,www.qop.com,www.plavion-sample.com, www.fismet-sample.com (busy but clear CTAs), www.yarmel-sample.com
Reason: We lost a lot of time to review over the holiday weekend. We need to have a chance to interact during business hours.
Target Market(s)
Small business to large enterprise
Industry/Entity Type
Business
Look and feel

```html
<!DOCTYPE html>
<html lang="en">
<head>
<meta charset="utf-8">
<title>Velquor – Com.AU</title>
<link rel="stylesheet" href="https://fonts.googleapis.com/css2?family=Oswald:wght@400&family=Ubuntu:wght@400;500;700&display=swap">
<style>
:root{
  --page:#f5f5f5;
  --band:#ececec;
  --navy:#13214f;
  --navy-deep:#0e1b45;
  --ink:#2a2a2a;
  --text:#4a4a4a;
  --muted:#8a8a8a;
  --link:#2a2f86;
  --orange:#f07a14;
  --orange-dark:#d9650a;
  --blue:#363f97;
  --blue-dark:#282f7c;
  --rule:#bfbfbf;
  --foot-link:#c4cadc;
  --badge:#9a9a9a;
}
*{margin:0;padding:0;box-sizing:border-box}
html,body{width:1200px;height:680px;overflow:hidden}
body{position:relative;background:var(--page);font-family:"Ubuntu",sans-serif;color:var(--text)}
.abs{position:absolute}
.heading{font-family:"Oswald",sans-serif;font-weight:400;color:var(--ink);white-space:nowrap}
.feature-title{left:171px;top:8px;font-size:34px}
.feature-rule{left:171px;top:59px;width:505px;height:2px;background:var(--rule)}
.slide-arrows{left:641px;top:26px}
.logo-box{left:171px;top:81px;width:119px;height:111px;background:#fff;border:1px solid #c9c9c9;display:flex;align-items:center;justify-content:center}
.logo-box .badge{width:90px;height:40px;background:#e0e0e0;border-radius:4px}
.feature-copy{left:310px;top:80px;width:372px;font-size:13px;line-height:22px;color:var(--text)}
.btn{height:29px;border-radius:5px;color:#fff;font-weight:500;font-size:14px;display:flex;align-items:center;justify-content:center;gap:8px;white-space:nowrap;box-shadow:0 1px 2px rgba(0,0,0,.25)}
.btn-orange{background:linear-gradient(var(--orange),var(--orange-dark))}
.btn-blue{background:linear-gradient(var(--blue),var(--blue-dark))}
.btn svg{width:12px;height:8px}
.divider{left:704px;top:0;width:8px;height:230px;background:linear-gradient(90deg,rgba(0,0,0,0),rgba(0,0,0,.05),rgba(0,0,0,0))}
.news-title{left:797px;top:2px;font-size:34px}
.news-icon{left:746px;top:15px}
.news-rule{left:746px;top:59px;width:262px;height:2px;background:var(--rule)}
.news-item{left:746px;width:262px}
.news-item h3{font-size:14.5px;font-weight:700;color:var(--link);line-height:17px}
.news-item time{display:block;font-size:11px;color:var(--muted);margin-top:2px}
.dash{left:746px;width:262px;border-top:1px dashed #b5b5b5}
.partners{left:0;top:312px;width:1200px;height:100px;background:var(--band);border-top:1px solid var(--navy)}
.partner-badge{position:absolute;background:var(--badge);opacity:.75}
.footer{left:0;top:404px;width:1200px;height:276px}
.footer-bg{position:absolute;left:0;top:8px;width:1200px;height:268px;background:var(--navy-deep)}
.world-map{position:absolute;left:440px;top:30px;width:340px;height:230px;border-radius:50%;background:radial-gradient(ellipse,rgba(60,80,140,.35),rgba(14,27,69,0) 70%)}
.col h4{font-family:"Oswald",sans-serif;font-weight:400;font-size:21px;color:#fff;margin-bottom:10px;white-space:nowrap}
.col ul{list-style:none}
.col li{font-size:12px;color:var(--foot-link);white-space:nowrap}
.col.tall li{line-height:25px}
.col.short li{line-height:20px}
.brand{left:175px;top:612px;display:flex;align-items:center;gap:6px;color:#6f7ca8;font-size:20px;font-weight:500}
.brand .dot{width:20px;height:20px;border-radius:50%;border:2px solid #6f7ca8}
.legal{left:286px;top:610px;font-size:10px;line-height:20px;color:var(--foot-link)}
.mail-title{left:832px;top:603px;font-family:"Oswald",sans-serif;font-size:19px;color:#fff}
.subscribe{left:921px;top:607px;width:88px;height:26px;font-size:13px;font-weight:700;letter-spacing:.3px}
.mail-note{left:832px;top:634px;font-size:11px;color:#8e98b8}
</style>
</head>
<body>

<h1 class="abs heading feature-title">Com.AU - It does what it says on box</h1>
<div class="abs feature-rule"></div>
<svg class="abs slide-arrows" width="30" height="20" viewBox="0 0 30 20" aria-hidden="true">
  <path d="M12 0 L12 20 L1 10Z" fill="var(--orange)"/>
  <path d="M17 0 L17 20 L28 10Z" fill="var(--blue)"/>
</svg>

<div class="abs logo-box" role="img" aria-label="Domain administration badge"><span class="badge"></span></div>
<p class="abs feature-copy">.AUstralia's home on the Internet - COM.AU is trusted by users around the world due to the strict registration policies which maintain the integrity &amp; accuracy of the entire .AU namespace. With over 2+ million registrations, .COM.AU is the best domain to help your business reach the Australian audience.</p>

<a class="abs btn btn-orange" style="left:172px;top:220px;width:242px">Register your .COM.AU Today!
  <svg viewBox="0 0 12 8"><path d="M0 0H12L6 8Z" fill="#fff"/></svg></a>
<a class="abs btn btn-blue" style="left:427px;top:220px;width:119px">Read More
  <svg viewBox="0 0 12 8"><path d="M0 0H12L6 8Z" fill="#fff"/></svg></a>

<div class="abs divider"></div>

<svg class="abs news-icon" width="34" height="28" viewBox="0 0 34 28" aria-hidden="true">
  <rect x="1" y="1" width="30" height="24" rx="2" fill="#fff" stroke="#333" stroke-width="2"/>
  <rect x="5" y="5" width="22" height="5" fill="#333"/>
  <path d="M5 14H27M5 18H27M5 22H20" stroke="#333" stroke-width="1.5"/>
</svg>
<h2 class="abs heading news-title">Latest News</h2>
<div class="abs news-rule"></div>

<article class="abs news-item" style="top:76px">
  <h3>Velquor Corporation Announces .CO Accreditation -</h3>
  <time>April 13, 2012</time>
</article>
<div class="abs dash" style="top:137px"></div>
<article class="abs news-item" style="top:146px">
  <h3>Velquor Attracts Leading Senior Channel Manager Marisol Keeton</h3>
  <time>April 13, 2012</time>
</article>
<div class="abs dash" style="top:204px"></div>

<a class="abs btn btn-orange" style="left:742px;top:220px;width:116px">Read More
  <svg viewBox="0 0 12 8"><path d="M0 0H12L6 8Z" fill="#fff"/></svg></a>

<section class="abs partners" aria-label="Accreditations">
  <svg class="abs" style="left:174px;top:36px" width="16" height="26" viewBox="0 0 16 26" aria-hidden="true"><path d="M14 2L4 13L14 24" fill="none" stroke="#8a8a8a" stroke-width="4"/></svg>
  <span class="partner-badge" role="img" aria-label="Accreditation badge" style="left:212px;top:36px;width:58px;height:24px;border-radius:3px"></span>
  <span class="partner-badge" role="img" aria-label="Accreditation badge" style="left:304px;top:22px;width:62px;height:44px;border-radius:50%"></span>
  <span class="partner-badge" role="img" aria-label="Provider badge" style="left:401px;top:32px;width:83px;height:32px;border-radius:4px"></span>
  <span class="partner-badge" role="img" aria-label="Accreditation badge" style="left:518px;top:38px;width:74px;height:22px;border-radius:3px"></span>
  <span class="partner-badge" role="img" aria-label="Accreditation badge" style="left:630px;top:24px;width:48px;height:52px;border-radius:50%"></span>
  <span class="partner-badge" role="img" aria-label="Registrar badge" style="left:713px;top:24px;width:47px;height:55px;border-radius:2px"></span>
  <span class="partner-badge" role="img" aria-label="Accreditation badge" style="left:805px;top:24px;width:44px;height:44px;border-radius:50%"></span>
  <span class="partner-badge" role="img" aria-label="Accreditation badge" style="left:893px;top:26px;width:66px;height:40px;border-radius:4px"></span>
  <svg class="abs" style="left:989px;top:36px" width="16" height="26" viewBox="0 0 16 26" aria-hidden="true"><path d="M2 2L12 13L2 24" fill="none" stroke="var(--orange)" stroke-width="4"/></svg>
</section>

<footer class="abs footer">
  <svg class="abs" style="left:0;top:0" width="1200" height="10" viewBox="0 0 1200 10" preserveAspectRatio="none" aria-hidden="true">
    <path d="M0 10 Q7.5 0 15 10 T30 10 T45 10 T60 10 T75 10 T90 10 T105 10 T120 10 T135 10 T150 10 T165 10 T180 10 T195 10 T210 10 T225 10 T240 10 T255 10 T270 10 T285 10 T300 10 T315 10 T330 10 T345 10 T360 10 T375 10 T390 10 T405 10 T420 10 T435 10 T450 10 T465 10 T480 10 T495 10 T510 10 T525 10 T540 10 T555 10 T570 10 T585 10 T600 10 T615 10 T630 10 T645 10 T660 10 T675 10 T690 10 T705 10 T720 10 T735 10 T750 10 T765 10 T780 10 T795 10 T810 10 T825 10 T840 10 T855 10 T870 10 T885 10 T900 10 T915 10 T930 10 T945 10 T960 10 T975 10 T990 10 T1005 10 T1020 10 T1035 10 T1050 10 T1065 10 T1080 10 T1095 10 T1110 10 T1125 10 T1140 10 T1155 10 T1170 10 T1185 10 T1200 10Z" fill="var(--navy-deep)"/>
  </svg>
  <div class="footer-bg">
    <div class="world-map" role="img" aria-label="Faint dotted world map"></div>
  </div>
</footer>

<nav class="abs col tall" style="left:175px;top:448px">
  <h4>Domain</h4>
  <ul><li>Name Registration</li><li>Name Services</li><li>New Top Level Domains</li><li>International Phone Numbers</li></ul>
</nav>
<nav class="abs col tall" style="left:346px;top:446px">
  <h4>Hosting</h4>
  <ul><li>Web Hosting Packages</li><li>Email Hosting Packages</li><li>Customer Login</li></ul>
</nav>
<nav class="abs col short" style="left:515px;top:448px">
  <h4>Resellers</h4>
  <ul><li>API Solution</li><li>Reseller Support</li><li>Signup</li></ul>
</nav>
<nav class="abs col short" style="left:684px;top:448px">
  <h4>About Velquor</h4>
  <ul><li>Our Company</li><li>Our People</li><li>Our Technology</li></ul>
</nav>
<nav class="abs col short" style="left:862px;top:446px">
  <h4>Quick Support</h4>
  <ul><li>Domain Support</li><li>DNS Support</li><li>Hosting Support</li></ul>
</nav>

<div class="abs brand"><span class="dot"></span>velquor</div>
<p class="abs legal">Copyright © 2012-2014 Velquor Corporation All Rights Reserved.<br>Contact Us | FAQ | Privacy Policy | Terms of Services | Sitemap</p>

<h4 class="abs mail-title">Mailing List</h4>
<a class="abs btn btn-orange subscribe">SUBSCRIBE</a>
<p class="abs mail-note">Be alerted about breakthrough</p>

</body>
</html>
```